VELORA Brisbane Tiling Service

My name is Milos Brendt i need a business card for a new company. We are wall and floor tilers based in Brisbane, our company is Velorix Brisbane Tiling Service.
We would like a logo from our website used on our cards. Our website is www.velorix.com.au

I would like my Chatterbook and Postwave accounts on my card.

Industry/Entity Type

Business

Colors
0692cd
3176b5
33a6d7
85cae6

```html
<!DOCTYPE html>
<html lang="en">
<head>
<meta charset="utf-8">
<title>Velorix Brisbane Tiling Service – Business Card</title>
<link rel="stylesheet" href="https://fonts.googleapis.com/css2?family=Open+Sans:wght@400;600;700&display=swap">
<style>
  :root {
    --brand-blue: #0692cd;
    --mid-blue: #3176b5;
    --sky-blue: #33a6d7;
    --pale-blue: #85cae6;
    --navy: #0f2a56;
    --navy-deep: #0a1f44;
    --paper: #f7f8f8;
    --ink: #16233d;
    --stage: #eef1f4;
  }
  * { box-sizing: border-box; margin: 0; padding: 0; }
  html, body { width: 1060px; height: 1200px; overflow: hidden; }
  body {
    background: var(--stage);
    font-family: "Open Sans", Arial, sans-serif;
    position: relative;
  }

  .card {
    position: absolute;
    width: 600px;
    height: 343px;
    border-radius: 4px;
    overflow: hidden;
    box-shadow: 0 10px 26px rgba(10, 31, 68, 0.22);
  }

  /* Front */
  .card-front { left: 60px; top: 60px; background: var(--paper); }
  .card-front .bands { position: absolute; inset: 0; }
  .front-logo {
    position: absolute; left: 40px; top: 36px;
    display: flex; align-items: center; gap: 12px;
  }
  .logo-square {
    width: 58px; height: 58px; background: var(--brand-blue); border-radius: 3px;
  }
  .logo-text { line-height: 1; }
  .logo-name {
    font-size: 52px; font-weight: 400; color: var(--brand-blue); letter-spacing: 1px;
  }
  .logo-tag {
    font-size: 19px; color: var(--mid-blue); margin-top: 2px; letter-spacing: 0.3px;
  }
  .person {
    position: absolute; left: 300px; top: 112px; color: var(--ink); line-height: 1.25;
  }
  .person-name { font-size: 22px; font-weight: 700; }
  .person-role { font-size: 13px; font-weight: 400; color: #33415c; }
  .contacts {
    position: absolute; left: 170px; top: 224px;
    display: grid; grid-template-columns: 190px 200px; row-gap: 8px;
    color: #fff; font-size: 14px; font-weight: 600;
  }
  .contact { display: flex; align-items: center; gap: 7px; }
  .contact-dot {
    width: 14px; height: 14px; border-radius: 50%; background: #fff; flex: none;
    display: flex; align-items: center; justify-content: center;
  }
  .website {
    position: absolute; right: 44px; bottom: 18px;
    color: #fff; font-size: 18px; font-weight: 700; letter-spacing: 0.3px;
  }

  /* Back */
  .card-back {
    left: 400px; top: 450px;
    background: radial-gradient(ellipse at 40% 40%, #1b3d74 0%, var(--navy) 55%, var(--navy-deep) 100%);
    display: flex; align-items: center; justify-content: center;
  }
  .card-back .logo-square { background: #fff; width: 64px; height: 64px; }
  .card-back .logo-name { color: #fff; font-size: 58px; }
  .card-back .logo-tag { color: #fff; font-size: 21px; }
  .back-logo { display: flex; align-items: center; gap: 12px; }

  /* Logo lockup */
  .logo-lockup {
    position: absolute; left: 0; right: 0; top: 920px;
    display: flex; justify-content: center; align-items: center; gap: 16px;
  }
  .logo-lockup .logo-square {
    width: 124px; height: 124px;
    background: linear-gradient(135deg, var(--sky-blue), var(--mid-blue));
  }
  .logo-lockup .logo-name { font-size: 104px; color: var(--brand-blue); }
  .logo-lockup .logo-tag { font-size: 40px; color: var(--mid-blue); margin-top: 4px; }
</style>
</head>
<body>

  <section class="card card-front" aria-label="Business card front">
    <svg class="bands" width="600" height="343" viewBox="0 0 600 343" aria-hidden="true">
      <defs>
        <linearGradient id="blueBand" x1="0" y1="0" x2="1" y2="0">
          <stop offset="0" stop-color="#0692cd"/>
          <stop offset="1" stop-color="#3176b5"/>
        </linearGradient>
      </defs>
      <path d="M0,202 Q260,170 600,170" fill="none" stroke="#0f2a56" stroke-width="3"/>
      <path d="M0,216 Q260,184 600,184 L600,343 L0,343 Z" fill="url(#blueBand)"/>
      <path d="M0,296 Q300,272 600,266 L600,343 L0,343 Z" fill="#0f2a56"/>
    </svg>

    <div class="front-logo">
      <div class="logo-square"></div>
      <div class="logo-text">
        <div class="logo-name">velorix</div>
        <div class="logo-tag">brisbane tiling service</div>
      </div>
    </div>

    <div class="person">
      <div class="person-name">Milos Brendt</div>
      <div class="person-role">Chief Executive Officer</div>
    </div>

    <div class="contacts">
      <div class="contact">
        <span class="contact-dot">
          <svg width="9" height="9" viewBox="0 0 24 24"><path fill="#3176b5" d="M6.6 10.8a15 15 0 0 0 6.6 6.6l2.2-2.2a1 1 0 0 1 1-.25 11.4 11.4 0 0 0 3.6.6 1 1 0 0 1 1 1V20a1 1 0 0 1-1 1A17 17 0 0 1 3 4a1 1 0 0 1 1-1h3.5a1 1 0 0 1 1 1c0 1.25.2 2.45.6 3.6a1 1 0 0 1-.25 1z"/></svg>
        </span>07-3555 0192
      </div>
      <div class="contact"><span class="contact-dot"></span>hello@velorix.com.au</div>
      <div class="contact"><span class="contact-dot"></span>chatterbook/velorix</div>
      <div class="contact"><span class="contact-dot"></span>postwave @velorix</div>
    </div>

    <div class="website">www.velorix.com.au</div>
  </section>

  <section class="card card-back" aria-label="Business card back">
    <div class="back-logo">
      <div class="logo-square"></div>
      <div class="logo-text">
        <div class="logo-name">velorix</div>
        <div class="logo-tag">brisbane tiling service</div>
      </div>
    </div>
  </section>

  <section class="logo-lockup" aria-label="Velorix logo">
    <div class="logo-square"></div>
    <div class="logo-text">
      <div class="logo-name">velorix</div>
      <div class="logo-tag">brisbane tiling service</div>
    </div>
  </section>

</body>
</html>
```